WordPress Website for BidLinks Agency

We are in need of a complete WordPress design.

We will be seeking new clients and we want them to have a great idea of what our business does when they get to the page along with the products and services we offer. Our current website is www.mossyharbor.com and it really needs an upgrade. Wordpress would be great but our owner knows HTML as well so he can go in and edit things later if need be. Please apply if you can show what a Search Engine Marketing company does and can explain this information to a lay person. Also, the website should be responsive so it fits mobile, tablet, and desktop settings while changing to these different widths.

Also, we are not an SEO company, per se but an SEM / PPC company that operates on Zorvic BidLinks, Plim Promos, Chatterwall Promos, and other PPC platforms.

Themes are fine just as long as the content and the visuals display what a search engine marketing company does. Really looking for clients to know exactly why a search engine marketing company does when the get to the site, why they should use a search engine marketing company, and the best way to contact us to get a quote.

Here are some other search engine marketing sites that I like in terms of the content and the layout to give an idea of what should be included on the site:
http://www.fendowlabs.com/
http://www.k9rworks.com/
http://www.boulderpartners.com/
http://www.vjnpromo.com/
http://www.halvorteam.com/
http://meetthepinecrew.com/

Please include my new phone number of the website: 866-555-0142.

Thank you, 
Walt 

Target Market(s)

We are a search engine marketing company looking for more clients and want to be able to explain what a search engine marketing company does in layman's terms.

Industry/Entity Type

Marketing

Font styles to use
Sans Serif

Requirements
Must have
• About Us Page
Services Page
Home Page
Success Stories Page
Blog
Social Media links / feeds
Visuals of products / services offered
Jobs page
Nice to have
• Responsive design
Client Login / Space on the site for monthly client payments / Link to CoinTap or Rivermoss

```html
<!DOCTYPE html>
<html lang="en">
<head>
<meta charset="utf-8">
<title>Privacy Policy – MossyHarbor</title>
<link rel="stylesheet" href="https://fonts.googleapis.com/css2?family=Source+Sans+3:wght@300;400;600;700&display=swap">
<style>
:root{
  --red:#e3161f;
  --ink:#444;
  --text:#5e5e5e;
  --page:#f5f5f5;
  --white:#fff;
  --footer:#2c2c2c;
  --footer-text:#e8e8e8;
  --bullet:#8a8a8a;
  --sky:#5bbfe8;
  --navy:#3a66b0;
  --teal:#1a86c8;
  --amber:#f39a1d;
  --coral:#e5553f;
  --badge-grey:#6f6f6f;
  --badge-blue:#1d6f9c;
}
*{box-sizing:border-box;margin:0;padding:0}
html,body{width:925px;height:1200px;overflow:hidden}
body{position:relative;background:var(--white);font-family:"Source Sans 3",sans-serif;color:var(--text)}
.page-band{position:absolute;left:0;top:321px;width:925px;height:645px;background:var(--page)}
.brand{position:absolute;left:91px;top:62px;font-size:20px;font-weight:600;color:var(--ink);line-height:1}
.social-top{position:absolute;right:91px;top:13px;display:flex;gap:3px}
.social-top span{width:28px;height:28px;border-radius:50%}
.nav{position:absolute;right:91px;top:70px;display:flex;gap:30px;font-size:13px;font-weight:300;color:var(--ink)}
.hero{position:absolute;left:91px;top:106px;width:742px;height:279px;
  background:radial-gradient(ellipse 230px 170px at 300px 120px,#f5a868 0%,#e08a63 35%,rgba(120,80,140,0) 75%),
  linear-gradient(110deg,#2d2c58 0%,#403f7a 40%,#365a86 65%,#4a4b86 100%);
  box-shadow:0 14px 16px -10px rgba(0,0,0,.25)}
.hero-caption{position:absolute;left:30px;top:186px;font-size:19px;font-weight:300;color:var(--white)}
.hero-dots{position:absolute;left:28px;top:247px;display:flex;gap:4px}
.hero-dots span{width:12px;height:12px;border-radius:50%;background:#c9c9c9}
.hero-dots span.active{background:var(--red)}
.policy{position:absolute;left:99px;top:420px;width:728px}
.policy h1{font-size:20px;font-weight:700;color:var(--red);margin-bottom:8px}
.policy p{font-size:11.7px;font-weight:400;line-height:23.2px;text-align:justify;letter-spacing:-.15px}
.policy p.gap{margin-bottom:23px}
.policy a{color:var(--red);text-decoration:none}
.footer{position:absolute;left:0;top:966px;width:925px;height:234px;background:var(--footer);color:var(--footer-text);font-weight:300}
.col-title{font-size:11.5px;font-weight:400;color:var(--white)}
.tweets{position:absolute;left:149px;top:17px;width:212px}
.tweet{position:relative;padding-left:23px;font-size:9.8px;line-height:19.2px;margin-top:8px}
.tweet+.tweet{border-top:1px solid #444;padding-top:6px;margin-top:6px}
.tweet::before{content:"";position:absolute;left:3px;top:6px;width:8px;height:8px;border-radius:50%;background:var(--bullet)}
.tweet+.tweet::before{top:12px}
.tweet .handle,.tweet .date{color:var(--red)}
.links{position:absolute;left:417px;top:17px;width:130px}
.links ul{list-style:none;font-size:9.6px;line-height:18.5px;margin:5px 0 10px}
.links li.current{color:var(--red)}
.follow{display:flex;gap:2px;margin-top:7px}
.follow span{width:27px;height:27px;border-radius:50%}
.newsletter{position:absolute;left:594px;top:19px;width:215px}
.newsletter p{font-size:9.6px;line-height:18.5px}
.newsletter .field{margin-top:9px;height:31px;background:var(--white);border-radius:2px}
.newsletter .subscribe{margin:9px 0 0 auto;width:67px;height:23px;background:var(--red);color:var(--white);font-size:9.5px;text-align:center;line-height:23px;font-weight:400}
.badge{position:absolute;top:170px;height:42px;border-radius:3px}
.badge.grey{left:598px;width:64px;background:var(--badge-grey)}
.badge.blue{left:698px;width:110px;background:var(--badge-blue)}
</style>
</head>
<body>
<div class="page-band"></div>

<header>
  <div class="brand">MossyHarbor</div>
  <div class="social-top">
    <span style="background:var(--sky)"></span>
    <span style="background:var(--navy)"></span>
    <span style="background:var(--teal)"></span>
  </div>
  <nav class="nav">
    <span>Home</span><span>About us</span><span>Services</span><span>Success stories</span><span>Blog</span><span>Contact us</span>
  </nav>
</header>

<section class="hero" role="img" aria-label="Banner image of a glowing padlock over a field of hexadecimal data">
  <div class="hero-caption">Privacy Policy</div>
  <div class="hero-dots"><span class="active"></span><span></span><span></span><span></span></div>
</section>

<main class="policy">
  <h1>Privacy Policy</h1>
  <p class="gap">We understand that many companies and individuals have information of a sensitive nature pertaining to them or their clients and thus we take great care to ensure the highest possible levels of privacy.To this end below are the details of our “Privacy Policy” which outlines our procedures on the collection and use of Client information.The Brightfield Marketing Institute will not provide any information, which you give us to any other organisation or individual without your express permission or legal compulsion such as a Court order.Any personal information which you volunteer to the Commissioner will be treated with the highest standards of security and confidentiality, strictly in accordance with the Data Protection Acts, 1988 &amp; 2003.</p>
  <p class="gap">The Brightfield Marketing Institute does not collect any personal data about you on this website, apart from information which you volunteer (for example by using our online feedback form). Any information which you provide in this way is not made available to any third parties, and is used by the Brightfield Marketing Institute only in line with the purpose for which you provided it.As part of routine administration, the Brightfield Marketing Institute collects statistical information such as page view, and browser statistics. Where possible these are collected anonymously, and are not on-sold or disclosed to others.All clients may request access to the personal details collected by the Brightfield Marketing Institute in relation to themselves and the use of services owned by them. The Brightfield Marketing Institute makes every effort to ensure that such details are always correct and up-to-date, and will amend any inaccuracies or changes to details on request.</p>
  <p>The Brightfield Marketing Institute does not retain clients' personal information longer than is necessary for the purposes of compliance with the law and routine administration.The Brightfield Marketing Institute keeps client information on controlled facilities, which are secured against unauthorised access. Proof of identity will be required before information is released to any person, including the client. The Brightfield Marketing Institute typically communicates with its clients through a combination of Phone, Written, Faxed and E-mail correspondence</p>
  <p>The Brightfield Marketing Institute is constantly improving and enhancing its services to clients, and may update this privacy policy from time to time. Any changes to the policy will be advised to clients.If you have any queries or comments concerning the privacy policy, please <a href="#">Contact Us.</a></p>
</main>

<footer class="footer">
  <div class="tweets">
    <div class="col-title">Latest Tweet</div>
    <div class="tweet">
      <span class="handle">@Smith</span> Orchard Lorem Ipsum is simply dummy text of the printing and typesetting industry. Lorem ipsum dolor sit amet, consectetur.<br><span class="date">June 29, 2013</span>
    </div>
    <div class="tweet">
      <span class="handle">@Smith</span> Orchard Lorem Ipsum is simply dummy text of the printing and typesetting industry. Lorem ipsum dolor sit amet, consectetur.<br><span class="date">June 29, 2013</span>
    </div>
  </div>

  <div class="links">
    <div class="col-title">Terms &amp; Privacy</div>
    <ul><li>Terms and Conditions</li><li class="current">Privacy Statement</li></ul>
    <div class="col-title">The Impact</div>
    <ul><li>The Numbers</li><li>Annual Report</li></ul>
    <div class="col-title">Follow us on</div>
    <div class="follow">
      <span style="background:var(--sky)"></span>
      <span style="background:var(--navy)"></span>
      <span style="background:var(--amber)"></span>
      <span style="background:var(--coral)"></span>
    </div>
  </div>

  <div class="newsletter">
    <p>Stay in touch with us by signing up for our quarterly newsletter!</p>
    <div class="field"></div>
    <div class="subscribe">SUBSCRIBE</div>
  </div>

  <div class="badge grey" role="img" aria-label="Partner badge"></div>
  <div class="badge blue" role="img" aria-label="Accreditation badge"></div>
</footer>
</body>
</html>
```